Harborline Auto LLC

Car Dealer Customer Service
Address: 2874 Cresthaven Road, Shelbyville, TN 37162
web: www.harborlineautoxq.net
email: harborlineautoxq@mailnest.example
Phone: (931) 555-0148
Phone: (629) 555-0173

```html
<!DOCTYPE html>
<html lang="en">
<head>
<meta charset="utf-8">
<title>Harborline Auto – Business Card</title>
<link href="https://fonts.googleapis.com/css2?family=Montserrat:wght@400;700&display=swap" rel="stylesheet">
<style>
  :root {
    --page: #8f8f8f;
    --white: #ffffff;
    --blue: #2790c9;
    --blue-deep: #1c7bad;
    --blue-ink: #1f78ac;
    --gold: #ecb443;
  }
  * { box-sizing: border-box; margin: 0; padding: 0; }
  html, body { width: 1160px; height: 1200px; overflow: hidden; }
  body {
    background: var(--page);
    font-family: "Montserrat", Arial, sans-serif;
    position: relative;
  }
  .card {
    position: absolute;
    left: 199px;
    width: 777px;
    height: 441px;
    overflow: hidden;
  }
  .card--front { top: 105px; background: var(--white); }
  .card--back { top: 634px; background: var(--blue-deep); }

  .wave { position: absolute; inset: 0; width: 100%; height: 100%; }

  .brand {
    position: absolute;
    text-align: center;
    font-weight: 700;
    letter-spacing: 0.5px;
    white-space: nowrap;
    line-height: 1;
  }
  .brand__dot { border-radius: 50%; position: absolute; }

  .card--front .brand__dot {
    left: 120px; top: 58px; width: 122px; height: 122px;
    background: var(--blue);
  }
  .card--front .brand__name {
    left: 0; width: 362px; top: 190px;
    font-size: 26px; color: var(--blue-ink);
  }

  .contact {
    position: absolute;
    right: 28px;
    top: 190px;
    color: var(--white);
    text-align: right;
    font-size: 18.5px;
    line-height: 28px;
  }
  .contact__address { margin-bottom: 10px; }
  .contact__line {
    display: flex;
    justify-content: flex-end;
    align-items: center;
    gap: 9px;
    height: 31px;
  }
  .contact__icon { width: 16px; height: 16px; flex: none; }

  .card--back .brand__dot {
    left: 280px; top: 88px; width: 216px; height: 216px;
    background: var(--white);
  }
  .card--back .brand__name {
    left: 0; width: 777px; top: 314px;
    font-size: 46px; color: var(--white);
  }
</style>
</head>
<body>

<section class="card card--front" aria-label="Business card front">
  <svg class="wave" viewBox="0 0 1270 721" preserveAspectRatio="none" aria-hidden="true">
    <path fill="var(--blue)" d="M0,590 C250,610 450,520 600,430 C720,300 950,170 1270,164 L1270,721 L0,721 Z"/>
    <path fill="var(--gold)" d="M0,504 C250,545 450,480 595,405 C450,492 250,585 0,565 Z"/>
    <path fill="var(--gold)" d="M647,369 C760,275 980,150 1270,150 L1270,100 C1080,105 850,220 647,369 Z"/>
  </svg>

  <div class="brand">
    <span class="brand__dot"></span>
  </div>
  <div class="brand brand__name">HARBORLINE AUTO</div>

  <div class="contact">
    <p class="contact__address">Car Dealer Customer Service<br>2874 Cresthaven Road<br>Shelbyville, TN 37162</p>
    <p class="contact__line">(931) 555-0148
      <svg class="contact__icon" viewBox="0 0 16 16" aria-hidden="true"><path fill="var(--white)" d="M3.5 1.5l2.5 0.5 1 3-1.5 1.2a8 8 0 0 0 4.3 4.3L11 9l3 1 .5 2.5-2 2C7 14 2 9 1.5 3.5z"/></svg>
    </p>
    <p class="contact__line">(629) 555-0173
      <svg class="contact__icon" viewBox="0 0 16 16" aria-hidden="true"><path fill="var(--white)" d="M1 5c2-3 12-3 14 0l-1 2-3-1V4H5v2L2 7zM4 8h8l2 6H2z"/></svg>
    </p>
    <p class="contact__line">harborlineautoxq@mailnest.example
      <svg class="contact__icon" viewBox="0 0 16 16" aria-hidden="true"><path fill="var(--white)" d="M1 3h14v10H1z"/><path fill="none" stroke="var(--blue)" stroke-width="1.3" d="M1.5 3.5L8 9l6.5-5.5M1.5 12.5l4.5-4.5M14.5 12.5L10 8"/></svg>
    </p>
    <p class="contact__line">www.harborlineautoxq.net
      <svg class="contact__icon" viewBox="0 0 16 16" aria-hidden="true"><circle cx="8" cy="8" r="7" fill="var(--white)"/><path fill="none" stroke="var(--blue)" stroke-width="1.1" d="M1 8h14M8 1c-3 3-3 11 0 14M8 1c3 3 3 11 0 14"/></svg>
    </p>
  </div>
</section>

<section class="card card--back" aria-label="Business card back">
  <div class="brand">
    <span class="brand__dot"></span>
  </div>
  <div class="brand brand__name">HARBORLINE AUTO</div>
</section>

</body>
</html>
```